Cruise Booking Website

Cruise search and booking website

This project is a redesign of a cruise booking website we did a few years ago.

The current website is located here: http://voyage.pylonworks.example/en/

It's not fully functional but gives you ad idea how miserable the old design was.

All the information about cruises, cruise lines, destinations, ports and shore excursions will be similar to http://www.sailquest.example/
Actual search pages (form, results, single result, sailing and cabin selection, ship info, booking) will have EXACTLY the same info as sailquest.example

We like the style of http://harborfleetdesk.example, it's quite modern, good spacing, not overloaded with information. So you can use it as an example of what we like, not what we want as a final result for us. Please, don't copy it. The result should not be possible to resemble the harborfleetdesk.example, because our site has to be unique. This is important!
If you submit a design that clearly reminds another cruise site it will be rejected!

Also the mockup provided is just to give you the basic structure and show what information has to be present on the page. It doesn't mean the layout has to be the same as a mockup. The layout is up to the designer.

I've updated the mockup to be more generic so it doesn't confuse you:
https://files.boxvault.example/s/k7m2qp9wz4hx/Home%20page.png

When you're adding social sharing icons like plazanet/chirpline you have to use chinese ones instead:
https://files.boxvault.example/s/t3nr8vx5lc2e/chinese-social-icons.png
Originals: http://minilk.example/qR7t

We'll start with home page first and after it's approved inner pages can be designed.

I know the cost of the project doesn't look high, but the task is straight forward and doesn't require to be very original, it's better to follow existing design and layout patterns that proved to work well.
That's why I encourage you to choose a template to build the design on top of one of https://themeparlor.example/ themes if it will save the design work, will be easier and faster for you. So it will be more like a customization than a new design from scratch.

Mockups, site map and logo files:
- https://files.boxvault.example/sh/h48dm2rs73fkpw/QvnbW2Xz8e

Website tree:
- https://sheets.papernest.example/document/d/7xPqR2mLw9sTk4VbN8cHj3YzA6eUf5GdKo1iMnBv/edit?usp=sharing
Updates

So far a lot of designs are just copying http://www.harborfleetdesk.example/ - we don't like it!

We like the style of harborfleetdesk.example, it's quite modern, good spacing, not overloaded with information. So you can use it as an example of what we like, not what we want as a final result for us. Please, don't copy it. The result should not be possible to resemble the harborfleetdesk.example, because our site has to be unique. This is important!

Target Market(s)

Chinese travellers

Industry/Entity Type

Build

Requirements
Must have
• * White, blue and red
* Large spacing, not too much information cramped into a small space like sailquest.example or the current website
* More "hidden" info in popups, tabs and so on, so not to many things are visible at the same time
* Compatible with kestrel scaffold styling (for easier coding):
- http://kestrelkit.codeshelf.example/scaffold/index.html
- http://skinmarket.example/
* Feel free to propose to build the design on top of one of https://themeparlor.example/ themes if it will save the design work, will be easier and faster for you

```html
<!DOCTYPE html>
<html lang="en">
<head>
<meta charset="utf-8">
<title>Bluewake Voyages – Deals</title>
<link rel="stylesheet" href="https://fonts.googleapis.com/css2?family=Source+Sans+3:wght@400;600;700&display=swap">
<style>
:root{
  --page-blue:#2a6aa8;
  --page-glow:#dbe9f5;
  --brand:#1b5e9e;
  --brand-dark:#0f4a85;
  --nav-top:#2f86cf;
  --nav-bottom:#135fa6;
  --nav-active:#3a9ae0;
  --orange:#f58a1f;
  --orange-dark:#e06f0c;
  --panel:#2b76bd;
  --panel-edge:#1f5f9e;
  --grey-bg:#f1f2f3;
  --grey-line:#dcdfe2;
  --text:#3b3f44;
  --footer:#4a7fb2;
  --footer-bar:#3d6fa0;
  --white:#ffffff;
}
*{box-sizing:border-box;margin:0;padding:0}
html,body{width:971px;height:1200px;overflow:hidden}
body{
  font-family:"Source Sans 3",sans-serif;color:var(--text);position:relative;
  background:radial-gradient(ellipse 560px 700px at 485px 420px,var(--page-glow) 0%,#8fb6da 45%,var(--page-blue) 100%);
}
.page{position:absolute;left:146px;top:0;width:680px;height:1200px;background:var(--white)}
.abs{position:absolute}

/* header */
.brand{left:12px;top:26px;display:flex;align-items:center;gap:8px}
.brand-dot{width:36px;height:36px;border-radius:50%;background:var(--brand)}
.brand-name{font-size:24px;font-weight:700;color:var(--brand);line-height:1}
.brand-url{font-size:9px;color:var(--brand);font-weight:600;margin-top:3px}
.account{left:497px;top:13px;font-size:10px;color:var(--brand)}
.account span{margin:0 6px;color:#888}
.social{left:585px;top:10px;display:flex;gap:4px}
.social i{display:block;width:18px;height:18px;border-radius:4px}
.call{left:368px;top:41px;display:flex;align-items:center;gap:8px}
.call-phone{font-size:16px;font-weight:700;color:var(--brand);line-height:1}
.call-note{font-size:13px;color:#333;line-height:1.2}
.search{left:506px;top:53px;width:160px;height:18px;border:1px solid #cfd3d7;border-radius:3px;font-size:7px;color:#888;padding:4px 8px;background:linear-gradient(#fff,#f2f3f4)}
.search svg{position:absolute;right:6px;top:3px}

/* nav */
.nav{left:0;top:90px;width:680px;height:28px;background:linear-gradient(var(--nav-top),var(--nav-bottom));display:flex}
.nav a{color:#fff;font-size:8.5px;font-weight:700;text-decoration:none;display:flex;align-items:center;justify-content:center;height:28px;border-right:1px solid rgba(255,255,255,.15)}
.nav a.active{background:var(--nav-active)}

/* sidebar search */
.finder{left:15px;top:134px;width:200px;height:282px;background:var(--panel);border:2px solid var(--panel-edge);border-radius:3px;color:#dfeaf5}
.finder h2{position:absolute;left:0;top:0;width:100%;height:38px;font-size:18px;font-weight:400;color:#fff;padding:10px 0 0 18px;line-height:22px;border-bottom:1px solid rgba(255,255,255,.15)}
.lbl{position:absolute;font-size:9.5px;color:#d7e5f3;line-height:12px}
.field{height:19px;border-radius:2px;background:linear-gradient(#f3f4f5,#d9dcdf);border:1px solid #b8c2cc;font-size:7.5px;color:#333;padding:4px 7px;position:absolute;line-height:10px}
.field::after{content:"";position:absolute;right:0;top:0;width:16px;height:100%;border-left:1px solid #b8c2cc;background:linear-gradient(#f6f7f8,#e0e2e5)}
.field b{position:absolute;right:5px;top:5px;z-index:1;width:0;height:0;border-left:3px solid transparent;border-right:3px solid transparent;border-bottom:3px solid #777}
.field b+b{top:10px;border-bottom:0;border-top:3px solid #777}
.finder h3{font-size:11px;font-weight:400;color:#fff;position:absolute;left:15px;top:170px;line-height:14px}
.senior{position:absolute;left:16px;top:224px;display:flex;align-items:center;gap:4px;font-size:7.5px;line-height:10px}
.check{width:9px;height:9px;background:#e9ecef;border:1px solid #aab}
.btn-search{position:absolute;left:16px;top:238px;width:170px;height:27px;background:linear-gradient(#fba23a,var(--orange-dark));border-radius:3px;color:#fff;font-size:12.5px;font-weight:600;text-align:center;line-height:27px}

/* newsletter */
.news{left:15px;top:434px;width:200px;height:240px;background:linear-gradient(#3a86cc,#1c63a8);border:2px solid var(--panel-edge);border-radius:3px;color:#fff}
.news-photo{position:absolute;left:10px;top:11px;width:176px;height:104px;border:3px solid #fff;background:linear-gradient(160deg,#5cb6d8 0%,#9fd0e0 45%,#e9d9c1 70%,#c47c58 100%)}
.news h3{position:absolute;left:18px;top:127px;font-size:11px;font-weight:700}
.news p{position:absolute;left:18px;top:146px;font-size:7.5px}
.email{position:absolute;left:18px;top:164px;width:170px;height:19px;background:#fff;border:1px solid #c8d3de;border-radius:2px;font-size:7.5px;color:#888;padding:4px 7px}
.btn-sub{position:absolute;left:18px;top:193px;width:71px;height:19px;background:#0f4478;border-radius:2px;font-size:8.5px;text-align:center;line-height:19px}
.rules{position:absolute;left:20px;top:218px;font-size:8.5px}

/* content */
.crumbs{left:234px;top:133px;font-size:8px;color:var(--brand)}
.hero{left:234px;top:156px;width:430px;height:219px;background:linear-gradient(120deg,#9fb3c4 0%,#d3dde6 35%,#8e969f 60%,#c7ced6 100%)}
.hero-cap{position:absolute;left:0;bottom:0;width:100%;height:42px;background:rgba(30,30,30,.82);color:#fff;font-size:16.5px;font-weight:700;padding-left:14px;line-height:42px}
.tabs{left:234px;top:387px;display:flex;gap:2px}
.tabs span{height:25px;font-size:7px;color:#fff;display:flex;align-items:center;justify-content:center;background:linear-gradient(#f99a2e,var(--orange-dark));border-radius:3px 3px 0 0}
.tabs span.on{background:linear-gradient(#1c6fba,var(--brand-dark))}
.grid{left:234px;top:412px;width:430px;height:490px;background:var(--grey-bg);border:1px solid var(--grey-line)}
.card{position:absolute;width:130px;height:108px;background:#fafafa;border:1px solid var(--grey-line)}
.card .shot{position:absolute;left:3px;top:3px;width:122px;height:70px}
.card .name{position:absolute;left:9px;top:78px;font-size:7.5px;color:var(--brand)}
.card .price{position:absolute;left:9px;top:91px;font-size:8.5px;color:var(--orange)}
.sea1{background:linear-gradient(#8aa5bd 0%,#c6d2dc 45%,#e8ebee 60%,#2d6d96 100%)}
.sea2{background:linear-gradient(#6a9fd4 0%,#bcd5ea 45%,#f1f1f1 65%,#256a9c 100%)}
.sea3{background:linear-gradient(#3d7cc0 0%,#7fb2dd 40%,#f0f4f7 60%,#1a5d8c 100%)}
.dusk{background:linear-gradient(#1b2e4a 0%,#384f70 45%,#d28a52 70%,#2a2a3a 100%)}
.palm{background:linear-gradient(#3b83c6 0%,#8cc0e3 50%,#1e8a9a 80%,#155e78 100%)}

/* partners */
.partners-title{left:12px;top:918px;font-size:13px;font-weight:700;color:var(--brand)}
.arrows{left:636px;top:917px;display:flex;gap:2px}
.arrows i{display:flex;align-items:center;justify-content:center;width:14px;height:14px;background:#d8dbde;border:1px solid #c4c8cc}
.partner{position:absolute;top:943px;width:100px;height:51px;border:1px solid #d3d6d9;background:#fff;display:flex;align-items:center;justify-content:center}
.partner i{display:block;width:58px;height:14px;border-radius:3px}

/* footer */
.footer{left:0;top:1011px;width:680px;height:155px;background:var(--footer);color:#fff}
.footer h4{position:absolute;font-size:11px;font-weight:600}
.links{position:absolute;list-style:none;font-size:7.3px;line-height:15.2px}
.about-badge{position:absolute;left:280px;top:52px;width:68px;height:68px;background:#fff;border:1px solid #d5dde6;display:flex;align-items:center;justify-content:center}
.about-badge i{width:34px;height:34px;border-radius:50%;background:var(--brand)}
.about-text{position:absolute;left:364px;top:59px;width:90px;font-size:8.5px;line-height:12.5px}
.contact{position:absolute;left:489px;top:48px;font-size:9px;line-height:13.5px}
.contact-row{position:absolute;left:489px;font-size:8.5px;display:flex;align-items:center;gap:5px}
.bottom{left:0;top:1166px;width:680px;height:34px;background:var(--footer-bar);color:#fff;font-size:7px;text-align:center;line-height:34px}
</style>
</head>
<body>
<div class="page">

  <header>
    <div class="abs brand">
      <div class="brand-dot"></div>
      <div><div class="brand-name">Bluewake Voyages</div><div class="brand-url">www.bluewake.example</div></div>
    </div>
    <div class="abs account">Sign in<span>|</span>Signup</div>
    <div class="abs social">
      <i style="background:#e0312b"></i><i style="background:#27a6d8"></i><i style="background:#f0a21a"></i><i style="background:#d93e3e"></i>
    </div>
    <div class="abs call">
      <svg width="26" height="26" viewBox="0 0 26 26"><circle cx="13" cy="13" r="12" fill="none" stroke="#777" stroke-width="1.4"/><path d="M9 7c-1 1-1 3 0 5l3 4c2 2 3 3 5 3l1-2-3-2-1 1-3-4 1-1-2-4z" fill="#777"/></svg>
      <div><div class="call-phone">400 818 252</div><div class="call-note">Call Us Today!</div></div>
    </div>
    <div class="abs search">SEARCH :
      <svg width="10" height="10" viewBox="0 0 10 10"><circle cx="4" cy="4" r="3" fill="none" stroke="#bbb" stroke-width="1.2"/><path d="M6.3 6.3 9 9" stroke="#bbb" stroke-width="1.2"/></svg>
    </div>
  </header>

  <nav class="abs nav">
    <a style="width:75px">HOME</a>
    <a style="width:113px">DESTINATIONS</a>
    <a style="width:92px">CRUISE LINES</a>
    <a style="width:88px">CRUISE INFO</a>
    <a class="active" style="width:65px">DEALS</a>
    <a style="width:103px">ONLINE BOOKING</a>
    <a style="width:74px">CONTACT US</a>
    <a style="width:70px;border-right:0">BLOG</a>
  </nav>

  <aside class="abs finder">
    <h2>Find Your Cruise</h2>
    <div class="lbl" style="left:15px;top:47px">Destination</div>
    <div class="field" style="left:15px;top:59px;width:167px">Destination name<b></b><b></b></div>
    <div class="lbl" style="left:15px;top:84px">Length</div>
    <div class="lbl" style="left:105px;top:84px">Month</div>
    <div class="field" style="left:15px;top:96px;width:75px">Length Area<b></b><b></b></div>
    <div class="field" style="left:105px;top:96px;width:77px"><b></b><b></b></div>
    <div class="lbl" style="left:13px;top:123px">Cruise Lines</div>
    <div class="field" style="left:13px;top:135px;width:169px">Any Cruise line<b></b><b></b></div>
    <h3>Number of Travelers</h3>
    <div class="lbl" style="left:15px;top:186px">Age 25+</div>
    <div class="lbl" style="left:105px;top:186px">Age 0 to 24</div>
    <div class="field" style="left:15px;top:198px;width:75px">5<b></b><b></b></div>
    <div class="field" style="left:105px;top:198px;width:77px">0<b></b><b></b></div>
    <div class="senior"><span class="check"></span>Check for senior rates</div>
    <div class="btn-search">Search Cruises</div>
  </aside>

  <aside class="abs news">
    <div class="news-photo" role="img" aria-label="Retired couple relaxing in deck chairs by a pool"></div>
    <h3>Cruise Deals Newsletter</h3>
    <p>Subscribe to the best Cruise deals Now!</p>
    <div class="email">Email :</div>
    <div class="btn-sub">Subscribe</div>
    <div class="rules">Contest Rules</div>
  </aside>

  <div class="abs crumbs">HOME &nbsp;<span style="color:#888">›</span>&nbsp; BREADCRUMBS</div>

  <section class="abs hero" role="img" aria-label="Two businessmen shaking hands in an office">
    <div class="hero-cap">EXCLUSIVE 3 DAY BAHAMAS CRUISE - ¥ 9000</div>
  </section>

  <div class="abs tabs">
    <span class="on" style="width:93px">LAST MINUTE</span>
    <span style="width:86px">BY CRUISE LINE</span>
    <span style="width:85px">PACKAGES</span>
    <span style="width:86px">RECOMMENDED</span>
  </div>

  <section class="abs grid">
    <div class="card" style="left:9px;top:9px"><div class="shot sea1" role="img" aria-label="Cruise ship docked by a city skyline"></div><div class="name">3 day cruise to the Bahamas</div><div class="price">¥ 9000</div></div>
    <div class="card" style="left:149px;top:9px"><div class="shot sea2" role="img" aria-label="Two cruise ships at a port"></div><div class="name">3 day cruise to the Bahamas</div><div class="price">¥ 9000</div></div>
    <div class="card" style="left:289px;top:9px"><div class="shot sea3" role="img" aria-label="Cruise ship on open sea"></div><div class="name">3 day cruise to the Bahamas</div><div class="price">¥ 9000</div></div>

    <div class="card" style="left:9px;top:129px"><div class="shot sea2" role="img" aria-label="Cruise ship from above"></div><div class="name">3 day cruise to the Bahamas</div><div class="price">¥ 9000</div></div>
    <div class="card" style="left:149px;top:129px"><div class="shot dusk" role="img" aria-label="Cruise ship lit up at night"></div><div class="name">3 day cruise to the Bahamas</div><div class="price">¥ 9000</div></div>
    <div class="card" style="left:289px;top:129px"><div class="shot dusk" role="img" aria-label="Cruise ship at sunset"></div><div class="name">3 day cruise to the Bahamas</div><div class="price">¥ 9000</div></div>

    <div class="card" style="left:9px;top:249px"><div class="shot palm" role="img" aria-label="Cruise ship seen past palm trees"></div><div class="name">3 day cruise to the Bahamas</div><div class="price">¥ 9000</div></div>
    <div class="card" style="left:149px;top:249px"><div class="shot sea3" role="img" aria-label="Large white cruise ship bow"></div><div class="name">3 day cruise to the Bahamas</div><div class="price">¥ 9000</div></div>
    <div class="card" style="left:289px;top:249px"><div class="shot sea1" role="img" aria-label="Colourfully painted cruise ship"></div><div class="name">3 day cruise to the Bahamas</div><div class="price">¥ 9000</div></div>

    <div class="card" style="left:9px;top:370px"><div class="shot sea1" role="img" aria-label="Cruise ship near a green coast"></div><div class="name">3 day cruise to the Bahamas</div><div class="price">¥ 9000</div></div>
    <div class="card" style="left:149px;top:370px"><div class="shot palm" role="img" aria-label="Cruise ship in a tropical bay"></div><div class="name">3 day cruise to the Bahamas</div><div class="price">¥ 9000</div></div>
    <div class="card" style="left:289px;top:370px"><div class="shot sea3" role="img" aria-label="Cruise ship sailing on deep blue water"></div><div class="name">3 day cruise to the Bahamas</div><div class="price">¥ 9000</div></div>
  </section>

  <h2 class="abs partners-title">OUR RELIABLE PARTNERS</h2>
  <div class="abs arrows">
    <i><svg width="6" height="8" viewBox="0 0 6 8"><path d="M5 0 1 4l4 4" fill="none" stroke="#fff" stroke-width="1.4"/></svg></i>
    <i><svg width="6" height="8" viewBox="0 0 6 8"><path d="M1 0l4 4-4 4" fill="none" stroke="#fff" stroke-width="1.4"/></svg></i>
  </div>
  <div class="partner" style="left:13px"><i style="background:#c8302c"></i></div>
  <div class="partner" style="left:124px"><i style="background:#1c58a8"></i></div>
  <div class="partner" style="left:235px"><i style="background:#4f5f74"></i></div>
  <div class="partner" style="left:346px"><i style="background:#ef9a2a"></i></div>
  <div class="partner" style="left:457px"><i style="background:#4aa3d8"></i></div>
  <div class="partner" style="left:568px"><i style="background:#2a6fb8"></i></div>

  <footer class="abs footer">
    <h4 style="left:22px;top:27px">Useful Pages</h4>
    <ul class="links" style="left:22px;top:46px">
      <li>About Us</li><li>Contact us</li><li>Blog</li><li>FAQ</li><li>Terms of Service</li><li>Payment info</li><li>Reward Points</li>
    </ul>
    <h4 style="left:154px;top:27px">Cruise Infov</h4>
    <ul class="links" style="left:155px;top:46px">
      <li>Cruise news</li><li>Visa</li><li>Honeymoon cruises</li><li>Firsttime on a Cruise</li>
    </ul>
    <h4 style="left:280px;top:31px">About bluewake.example</h4>
    <div class="about-badge"><i></i></div>
    <div class="about-text">We're the most advanced cruise booking providr in china.</div>
    <h4 style="left:489px;top:31px">Contact Us</h4>
    <div class="contact">Harbin Lantern Studio Ltd<br>Quayside Block 12, Tidewater Rd 8<br>Port Alder 20417 Coastland</div>
    <div class="contact-row" style="top:99px"><svg width="11" height="8" viewBox="0 0 11 8"><path d="M1 3c3-3 6-3 9 0l-2 1-1-1H4L3 4z M3 5h5l1 3H2z" fill="#fff"/></svg>(021) 604-3318 - (021) 604-3319</div>
    <div class="contact-row" style="top:117px"><svg width="11" height="8" viewBox="0 0 11 8"><rect x=".5" y=".5" width="10" height="7" fill="none" stroke="#fff"/><path d="M.5.5l5 4 5-4" fill="none" stroke="#fff"/></svg>hello@bluewake.example</div>
  </footer>
  <div class="abs bottom">© 2013. Bluewake. All rights reserved.</div>

</div>
</body>
</html>
```